Business card design needed

I would like a one sided black business card with the information provided above. Refer to my website www.brightvolleyracquets.com.au for an example of colors I have used for my site, would like to keep this consistent for my business cards also, I will upload my logo below.

I am a new small business that provides tennis customers with racquet re stringing, tennis strings and accessories.

Industry/Entity Type

Small Business

Contact Information for Business Card

Bright Volley Tennis

Owen Whitby
Managing Director

brightvolleyracquets@mailbox.example
www.brightvolleyracquets.com.au
0491 726 305

Racquet Restringing/Tennis Strings/Accessories

Requirements
Must have
• Must have my logo and card must be black

```html
<!DOCTYPE html>
<html lang="en">
<head>
<meta charset="utf-8">
<title>Bright Volley Tennis – Business Card</title>
<link rel="stylesheet" href="https://fonts.googleapis.com/css2?family=Roboto:wght@400;700&display=swap">
<style>
  :root {
    --backdrop: #8a5a38;
    --card-black: #000000;
    --lime: #b6d334;
    --band-blue: #6f7fc4;
    --text-white: #ffffff;
    --text-dark: #1a1a1a;
  }
  * { margin: 0; padding: 0; box-sizing: border-box; }
  html, body {
    width: 1200px;
    height: 475px;
    overflow: hidden;
  }
  body {
    position: relative;
    background: var(--backdrop);
    font-family: "Roboto", Arial, sans-serif;
  }
  .card {
    position: absolute;
    top: 89px;
    width: 548px;
    height: 312px;
    border-radius: 20px;
    overflow: hidden;
    background: var(--card-black);
  }
  .card--front { left: 31px; }
  .card--back { left: 607px; }

  .card__header-band {
    position: absolute;
    left: 0;
    right: 0;
    top: 0;
    height: 64px;
    background: linear-gradient(180deg, var(--lime) 0%, var(--lime) 70%, var(--band-blue) 100%);
  }

  .holder {
    position: absolute;
    right: 26px;
    top: 14px;
    text-align: left;
    color: var(--text-dark);
  }
  .holder__name {
    font-size: 18px;
    font-weight: 400;
    letter-spacing: 0.5px;
    text-transform: uppercase;
    line-height: 1.1;
  }
  .holder__title {
    font-size: 13px;
    line-height: 1.4;
  }

  .brand {
    position: absolute;
    display: flex;
    align-items: center;
    gap: 10px;
    color: var(--lime);
    font-weight: 700;
    text-transform: uppercase;
    white-space: nowrap;
  }
  .brand__mark {
    width: 34px;
    height: 34px;
    border-radius: 50%;
    background: var(--lime);
    flex: none;
  }
  .brand__name { font-size: 26px; letter-spacing: 0.5px; }
  .card--front .brand { left: 40px; top: 122px; }
  .card--back .brand { left: 50%; top: 118px; transform: translateX(-50%); }

  .contact {
    position: absolute;
    left: 39px;
    top: 219px;
    list-style: none;
    color: var(--text-white);
    font-size: 14px;
    line-height: 19px;
  }
  .contact__label { color: var(--lime); }

  .website {
    position: absolute;
    left: 0;
    right: 0;
    top: 236px;
    text-align: center;
    color: var(--text-white);
    font-size: 13px;
    letter-spacing: 1.6px;
  }
</style>
</head>
<body>
  <section class="card card--front" aria-label="Business card front">
    <div class="card__header-band" role="img" aria-label="Decorative lime and blue wave band"></div>

    <div class="holder">
      <p class="holder__name">Owen Whitby</p>
      <p class="holder__title">Managing Director</p>
    </div>

    <div class="brand">
      <span class="brand__mark"></span>
      <span class="brand__name">Bright Volley Tennis</span>
    </div>

    <ul class="contact">
      <li><span class="contact__label">p</span> : 0491 726 305</li>
      <li><span class="contact__label">e</span> : brightvolleyracquets@mailbox.example</li>
      <li><span class="contact__label">w</span>: www.brightvolleyracquets.com.au</li>
    </ul>
  </section>

  <section class="card card--back" aria-label="Business card back">
    <div class="brand">
      <span class="brand__mark"></span>
      <span class="brand__name">Bright Volley Tennis</span>
    </div>
    <p class="website">www.brightvolleyracquets.com.au</p>
  </section>
</body>
</html>
```